Neue Website fuer Software-Firma (CMS: Joomla, Responsive Design)
Zielgruppe
Die VARENTO ist ein Software- und Beratungshaus im Lager- und Produktionslogistikbereich. Unsere Kunden sind Industriefirmen und Logistikdienstleister, die ein oder mehrere Laeger bewirtschaften und dafuer eine Software und mobile Datenerfassung einsetzen. Fast alle unserer Kunden haben Korvan im Einsatz.
Aufgabenstellung
Unsere aktuelle Website wurde seit langem nicht mehr gepflegt und ist veraltet.
Wir moechten die neue Website gern mit dem CMS Joomla betreiben (ggf. waere auch Wordpress moeglich). Gern koennen Sie als Basis ein bereits existierendes (freies) Theme verwenden, wenn es entweder bereits alle Ansprueche erfuellt oder Sie es entsprechend anpassen.
Die neue Website soll in jedem Fall responsive sein, d.h. sowohl auf Desktop, Tablet und Smartphone funktionieren und das Design entsprechend anpassen.
Unsere aktuelle Seite steht unter www.varento-lagerwerk.example
Eine Seite, die uns besonders gut gefaellt, ist www.quelbrix.example (die sich auch teilweise an die gleichen Kunden richtet).
Wir moechten ein klares Design. Ein Beispiel, wie eines unserer Dashboards unserer Software aussieht, finden Sie anbei. Die Farbgestaltung darin wird jedoch noch geaendert. Sie wird eher in Richtung der Farbgestaltung der Quelbrix-Website gehen, jedoch immer noch grundsaetzlich hell sein. Evtl. koennen Sie Elemente daraus aufgreifen? Es soll in jedem Fall ersichtlich sein, dass Website und Software von der gleichen Firma sind.
Es soll moeglichst viel mit Grafiken gearbeitet werden – aehnlich der Quelbrix-Seite unter der Dia-Show. Diese muessen aber nicht zwingend farbig sein. Ein Mockup fuer einfarbige Grafiken unterhalb einer Diashow habe ich hier erstellt: https://hannelore07.seitenbau.example/meineseite-1 Bitte orientieren Sie sich aber nicht an dieser Seite selbst – das war nur ein Probierbeispiel.
Desweiteren soll die Seite suchmaschinenfreundlich sein.
In Ihren Leistungen enthalten sein soll:
- Erstellung der Homepage incl.
o Menu (wie bei Quelbrix soll es ausklappbar sein und mind. 2 Ebenen koennen)
o Login-Button der einen externen Link aufruft
o Auswahl der Sprache (und damit Verlinkung zu jeweils der Homepage in der
ausgewaehlten Sprache
o Moeglichkeit zum Chat
o Suchfeld zum Durchsuchen aller S..

```html
<!DOCTYPE html>
<html lang="de">
<head>
<meta charset="utf-8">
<title>VARENTO – Software Solutions For Logistics</title>
<link rel="stylesheet" href="https://fonts.googleapis.com/css2?family=Open+Sans:wght@300;400;600;700&display=swap">
<style>
:root{
  --accent:#2ea3f2;
  --brand:#1f3c8c;
  --text:#666;
  --heading:#333;
  --light:#f4f4f4;
  --card-border:#ddd;
  --band:#8fd3eb;
  --form-bg:#e4e4e4;
  --field:#eeeeee;
  --footer:#222;
  --footer-bottom:#171717;
  --chat:#2e8ae6;
}
*{box-sizing:border-box;margin:0;padding:0}
html,body{width:1200px;height:2306px;overflow:hidden;background:#fff}
body{font-family:"Open Sans",sans-serif;color:var(--text);font-size:8px;line-height:1.7;position:relative}
.page{position:absolute;left:108px;top:0;width:984px;height:2306px;background:#fff;box-shadow:0 0 8px rgba(0,0,0,.12);overflow:hidden}
.abs{position:absolute}
.site-header{left:0;top:0;width:984px;height:54px;border-top:1px solid #555}
.brand{left:50px;top:8px;font-weight:700;font-size:22px;color:var(--brand);letter-spacing:.5px;line-height:26px}
.brand-tag{left:51px;top:33px;font-size:6px;color:var(--brand);letter-spacing:.4px}
.nav-icons{right:50px;top:20px;display:flex;gap:18px;align-items:center}
.hero{left:0;top:54px;width:984px;height:383px;background:linear-gradient(180deg,#d6e8f1 0%,#bfd7e4 35%,#7e9fb4 70%,#5d7d92 100%)}
.hero-title{left:0;width:984px;top:148px;text-align:center;font-weight:300;font-size:30px;color:#fff;letter-spacing:.3px}
.hero-btn{left:435px;top:199px;width:112px;height:32px;border:2px solid #fff;border-radius:3px;color:#fff;font-size:12px;text-align:center;line-height:28px}
.features{left:0;top:437px;width:984px;height:81px;background:var(--light)}
.feature{top:0;width:228px;text-align:center}
.feature svg{display:block;margin:10px auto 0}
.feature p{font-size:11px;color:#333;margin-top:11px}
.col h2{font-size:17px;font-weight:400;color:var(--heading);text-align:center;line-height:24px;margin-bottom:6px}
.col p{font-size:8px;line-height:15px;margin-bottom:9px}
.btn{border:2px solid var(--accent);color:var(--accent);border-radius:3px;font-size:12px;text-align:center}
.blog{left:0;top:804px;width:984px;height:427px;background:var(--light)}
.section-title{width:984px;left:0;text-align:center;font-size:16px;color:var(--heading);font-weight:400}
.card{width:277px;background:#fff;border:1px solid var(--card-border)}
.card .thumb{width:100%}
.card-body{padding:9px 12px 0}
.card h3{font-size:12px;font-weight:400;color:var(--heading);margin-bottom:5px}
.meta{font-size:8px;color:#555;margin-bottom:6px}
.card p{font-size:8px;line-height:15px}
.more{color:var(--accent);font-size:8px}
.band{left:0;top:1231px;width:984px;height:87px;background:var(--band)}
.band h2{left:156px;top:10px;font-size:20px;font-weight:400;color:#333}
.band p{left:156px;top:42px;width:300px;font-size:8px;line-height:15px;color:#555}
.band-btn{left:573px;top:16px;width:183px;height:32px;background:rgba(255,255,255,.2);color:#fff;font-size:12px;line-height:32px;text-align:center;border-radius:2px}
.quote{width:429px;height:101px;background:#f7f7f7}
.avatar{left:19px;top:19px;width:57px;height:57px;border-radius:50%;background:radial-gradient(circle at 50% 40%,#a9a9a9,#4a4a4a);border:3px solid #fff}
.quote-text{left:94px;top:18px;width:300px;font-size:8.5px;line-height:13px;color:#555}
.quote-name{left:94px;top:55px;font-size:8.5px;line-height:13px;color:#555}
.quote-name b{color:#333;font-weight:700}
.quote-name a{color:var(--accent);text-decoration:none}
.rule{left:208px;top:1621px;width:568px;height:1px;background:#ddd}
.partner{top:1639px}
.contact{left:0;top:1724px;width:984px;height:306px;background:var(--form-bg)}
.contact h2{left:50px;top:20px;font-size:17px;font-weight:400;color:#333}
.field{background:var(--field);font-size:8px;color:#999;padding:10px 10px}
.send{left:558px;top:252px;width:72px;height:32px;line-height:28px}
.info{left:658px;top:20px;width:282px}
.info h3{font-size:13px;font-weight:400;color:#333;margin-bottom:4px}
.info p{font-size:8px;line-height:15px;margin-bottom:9px}
.info b{color:#444}
.footer{left:0;top:2030px;width:984px;height:243px;background:var(--footer)}
.fcol h4{font-size:12px;font-weight:400;color:#fff;line-height:16px}
.fcol li{list-style:none;font-size:8px;line-height:17px;color:#aaa}
.footer-bottom{left:0;top:2273px;width:984px;height:33px;background:var(--footer-bottom)}
.copyright{left:50px;top:10px;font-size:8px;color:#777}
.social{right:50px;top:11px;display:flex;gap:16px}
.social span{width:11px;height:11px;border-radius:50%;background:#666;display:block}
.chat{left:1148px;top:529px;width:40px;height:40px;border-radius:50%;background:var(--chat);box-shadow:0 2px 6px rgba(0,0,0,.2)}
</style>
</head>
<body>
<div class="page">
  <header class="site-header abs">
    <div class="brand abs">VARENTO</div>
    <div class="brand-tag abs">Software Solutions For Logistics</div>
    <div class="nav-icons abs">
      <svg width="13" height="10" viewBox="0 0 13 10"><path d="M0 1h13M0 5h13M0 9h13" stroke="#666" stroke-width="1.3"/></svg>
      <svg width="10" height="11" viewBox="0 0 10 11"><circle cx="6" cy="4" r="3.2" fill="none" stroke="#666" stroke-width="1.2"/><path d="M3.7 6.3 1 9.5" stroke="#666" stroke-width="1.3"/></svg>
    </div>
  </header>

  <section class="hero abs" role="img" aria-label="Skyline mit Hochhäusern vor hellblauem Himmel">
    <h1 class="hero-title abs">Software Solutions For Logistics</h1>
    <div class="hero-btn abs">Mehr erfahren</div>
  </section>

  <section class="features abs">
    <div class="feature abs" style="left:36px">
      <svg width="26" height="22" viewBox="0 0 26 22"><ellipse cx="11" cy="9" rx="9" ry="7" fill="none" stroke="#2ea3f2" stroke-width="1.5"/><path d="M5 14 3 20l6-4M19 7a7 6 0 0 1 2 11l2 3-5-2" fill="none" stroke="#2ea3f2" stroke-width="1.5"/></svg>
      <p>Lorem Ipsum Domtata</p>
    </div>
    <div class="feature abs" style="left:263px">
      <svg width="24" height="24" viewBox="0 0 24 24"><rect x="2" y="2" width="20" height="14" fill="none" stroke="#2ea3f2" stroke-width="1.5"/><path d="M5 13l5-5 3 3 6-6M12 16v6M8 22l4-6 4 6" fill="none" stroke="#2ea3f2" stroke-width="1.5"/></svg>
      <p>Lorem Ipsum Domtata</p>
    </div>
    <div class="feature abs" style="left:492px">
      <svg width="24" height="24" viewBox="0 0 24 24"><path d="M3 5a4 4 0 0 0 6 4l11 11 2-2L11 7a4 4 0 0 0-4-6L9 4 7 6z" fill="none" stroke="#2ea3f2" stroke-width="1.5"/></svg>
      <p>Lorem Ipsum Domtata</p>
    </div>
    <div class="feature abs" style="left:719px">
      <svg width="24" height="24" viewBox="0 0 24 24"><rect x="2" y="4" width="17" height="17" fill="none" stroke="#2ea3f2" stroke-width="1.5"/><path d="M6 12l4 4 12-14" fill="none" stroke="#2ea3f2" stroke-width="1.8"/></svg>
      <p>Lorem Ipsum Domtata</p>
    </div>
  </section>

  <section class="col abs" style="left:50px;top:536px;width:429px">
    <h2>Softwarelösungen mit Qualität</h2>
    <p>Lorem ipsum dolor sit amet, consetetur sadipscing elitr, sed diam nonumy eirmod tempor invidunt ut et ea rebum.</p>
    <p>Lorem ipsum dolor sit amet, consetetur sadipscing elitr, sed diam nonumy eirmod tempor invidunt ut labore et dolore magna aliquyam erat, sed diam voluptua. At vero eos et accusam et justo duo dolores et ea rebum. Stet clita kasd gubergren, no sea takimata sanctus est Lorem ipsum dolor sit amet. Lorem ipsum dolor sit amet, consetetur sadipscing elitr, sed diam nonumy eirmod tempor invidunt ut labore et dolore magna aliquyam erat, sed diam voluptua. At vero eos et accusam et justo duo dolores et ea rebum.</p>
    <p>Stet clita kasd gubergren, no sea takimata sanctus est Lorem ipsum dolor sit amet. Lorem ipsum dolor sit amet, consetetur sadipscing elitr, sed diam nonumy eirmod tempor invidunt ut labore et dolore magna aliquyam erat, sed diam voluptua. At vero eos et accusam et justo duo dolores et ea rebum.</p>
  </section>
  <div class="btn abs" style="left:196px;top:755px;width:137px;height:30px;line-height:26px">Unsere Leistungen</div>

  <section class="col abs" style="left:505px;top:536px;width:429px">
    <h2>Wer sind wir?</h2>
    <p>Lorem ipsum dolor sit amet, consetetur sadipscing elitr, sed diam nonumy eirmod tempor invidunt ut et ea rebum. Stet clita kasd gubergren, no sea takimata sanctus est Lorem ipsum dolor sit amet.</p>
    <p>Lorem ipsum dolor sit amet, consetetur sadipscing elitr, sed diam nonumy eirmod tempor invidunt ut labore et dolore magna aliquyam erat, sed diam voluptua. At vero eos et accusam et justo duo dolores et ea rebum magna aliquyam erat, sed diam voluptua. At vero eos et accusam et justo duo dolores et ea rebum.</p>
  </section>
  <div class="btn abs" style="left:679px;top:671px;width:82px;height:30px;line-height:26px">Über uns</div>

  <section class="blog abs">
    <h2 class="section-title abs" style="top:24px">Neues aus unserem Blog</h2>
    <article class="card abs" style="left:50px;top:64px;height:336px">
      <div class="thumb" style="height:185px;background:linear-gradient(135deg,#3a3a3a,#7a7a7a 60%,#d8d8d8)" role="img" aria-label="Hand hält ein Smartphone vor dunklem Anzug"></div>
      <div class="card-body"><h3>Lorem Ipsum</h3><div class="meta">von tessak | Sep 23, 2017 | Uncategorized</div>
      <p>Lorem ipsum dolor sit amet, consetetur sadipscing elitr, sed diam nonumy eirmod tempor invidunt ut labore et dolore magna aliquyam erat, sed diam voluptua. At vero eos et accusam et justo duo dolores et ea rebum. Stet clita kasd gubergren, no sea takimata sanctus est…</p><span class="more">mehr lesen</span></div>
    </article>
    <article class="card abs" style="left:353px;top:64px;height:325px">
      <div class="thumb" style="height:173px;background:linear-gradient(180deg,#e8e8e8,#bdbdbd 55%,#8a8a8a)" role="img" aria-label="Helles Büro mit Schreibtisch und Stühlen"></div>
      <div class="card-body"><h3>Lorem Ipsum</h3><div class="meta">von tessak | Sep 23, 2017 | Uncategorized</div>
      <p>Lorem ipsum dolor sit amet, consetetur sadipscing elitr, sed diam nonumy eirmod tempor invidunt ut labore et dolore magna aliquyam erat, sed diam voluptua. At vero eos et accusam et justo duo dolores et ea rebum. Stet clita kasd gubergren, no sea takimata sanctus est…</p><span class="more">mehr lesen</span></div>
    </article>
    <article class="card abs" style="left:658px;top:64px;height:325px">
      <div class="thumb" style="height:173px;background:linear-gradient(180deg,#2a2a2a,#4a4a4a 70%,#d9d4cc)" role="img" aria-label="Zwei Monitore mit Designentwürfen"></div>
      <div class="card-body"><h3>Lorem Ipsum</h3><div class="meta">von tessak | Sep 23, 2017 | Uncategorized</div>
      <p>Lorem ipsum dolor sit amet, consetetur sadipscing elitr, sed diam nonumy eirmod tempor invidunt ut labore et dolore magna aliquyam erat, sed diam voluptua. At vero eos et accusam et justo duo dolores et ea rebum. Stet clita kasd gubergren, no sea takimata sanctus est…</p><span class="more">mehr lesen</span></div>
    </article>
  </section>

  <section class="band abs">
    <h2 class="abs">VARENTO Softwareentwicklung</h2>
    <p class="abs">Warehouse Management, Mobile Apps, Automation Integration, Korvan Development</p>
    <div class="band-btn abs">Jetzt Kontakt aufnehmen &nbsp;›</div>
  </section>

  <h2 class="section-title abs" style="top:1340px">Was unsere Kunden Sagen</h2>
  <div class="quote abs" style="left:50px;top:1377px"><div class="avatar abs" role="img" aria-label="Porträt einer Kundin"></div><p class="quote-text abs">Aenean consectetur ipsum ante, vel egestas enim tincidunt quis. Pellentesque vitae congue neque, vel mattis ante.</p><p class="quote-name abs"><b>Lorem Ipsum</b><br>Job Role, <a>Company</a></p></div>
  <div class="quote abs" style="left:505px;top:1377px"><div class="avatar abs" role="img" aria-label="Porträt eines Kunden"></div><p class="quote-text abs">Aenean consectetur ipsum ante, vel egestas enim tincidunt quis. Pellentesque vitae congue neque, vel mattis ante.</p><p class="quote-name abs"><b>Lorem Ipsum</b><br>Job Role, <a>Company</a></p></div>
  <div class="quote abs" style="left:50px;top:1491px"><div class="avatar abs" role="img" aria-label="Porträt eines Kunden"></div><p class="quote-text abs">Aenean consectetur ipsum ante, vel egestas enim tincidunt quis. Pellentesque vitae congue neque, vel mattis ante.</p><p class="quote-name abs"><b>Lorem Ipsum</b><br>Job Role, <a>Company</a></p></div>
  <div class="quote abs" style="left:505px;top:1491px"><div class="avatar abs" role="img" aria-label="Porträt einer Kundin"></div><p class="quote-text abs">Aenean consectetur ipsum ante, vel egestas enim tincidunt quis. Pellentesque vitae congue neque, vel mattis ante.</p><p class="quote-name abs"><b>Lorem Ipsum</b><br>Job Role, <a>Company</a></p></div>

  <div class="rule abs"></div>
  <div class="partner abs" style="left:307px;width:50px;height:58px;background:#cfd8dc;border-radius:4px" role="img" aria-label="Partnerabzeichen"></div>
  <div class="partner abs" style="left:412px;top:1650px;width:50px;height:40px;background:#dfe3e6;border-radius:50%" role="img" aria-label="Partnerabzeichen"></div>
  <div class="partner abs" style="left:515px;top:1644px;width:48px;height:48px;background:#d6e7ec;border-radius:4px" role="img" aria-label="Partnerabzeichen"></div>
  <div class="partner abs" style="left:612px;top:1652px;width:64px;height:28px;background:#e3dfe6;border-radius:3px" role="img" aria-label="Partnerabzeichen"></div>

  <section class="contact abs">
    <h2 class="abs">Jetzt Kontakt aufnehmen</h2>
    <div class="field abs" style="left:50px;top:49px;width:282px;height:31px">Name</div>
    <div class="field abs" style="left:349px;top:49px;width:281px;height:31px">E-Mail-Adresse</div>
    <div class="field abs" style="left:50px;top:98px;width:580px;height:32px">Betreff</div>
    <div class="field abs" style="left:50px;top:148px;width:580px;height:95px">Nachricht</div>
    <div class="btn send abs">Senden</div>
    <div class="info abs">
      <h3>More Info</h3>
      <p>sit amet, consectetur adipiscing elit. Integer placerat metus id orci facilisis, in luctus eros laoreet. Mauris interdum augue varius, faucibus massa id, imperdiet tortor. Donec vel tortor molestie, hendrerit sem a, hendrerit arcu. Aliquam erat volutpat. Proin varius eros eros, non condimentum nis.</p>
      <p><b>Address:</b> 890 Lorem Ipsum Street #12<br>San Francisco, California 65432</p>
      <p><b>Phone:</b> 123.4567.890</p>
      <p><b>Business Hours:</b> 8a-6:30p M-F, 9a-2p S-S</p>
    </div>
  </section>

  <footer class="footer abs">
    <div class="fcol abs" style="left:50px;top:56px"><h4>News</h4><ul><li>Aktuell</li><li>Archiv</li><li>Pressekontakt</li></ul></div>
    <div class="fcol abs" style="left:277px;top:56px"><h4>Unsere Produkte</h4><ul><li>Lorem Ipsum</li><li>Datan Dida</li><li>Forumsala</li><li>Counis</li></ul></div>
    <div class="fcol abs" style="left:505px;top:56px"><h4>Über VARENTO</h4><ul><li>Standorte</li><li>Wer sind wir?</li><li>Referenzen</li><li>Leistungen</li></ul></div>
    <div class="fcol abs" style="left:505px;top:159px"><h4>Karriere</h4><ul><li>Praktikum</li><li>Stellenangebote</li><li>Sonstiges</li></ul></div>
    <div class="fcol abs" style="left:733px;top:56px"><h4>Rechtliches</h4><ul><li>Impressum</li><li>Datenschutz</li></ul></div>
  </footer>
  <div class="footer-bottom abs">
    <div class="copyright abs">Copyright 2017 - Nordlicht Atelier</div>
    <div class="social abs"><span></span><span></span><span></span></div>
  </div>
</div>
<div class="chat abs">
  <svg width="40" height="40" viewBox="0 0 40 40"><path d="M14 15h12v8h-6l-3 3v-3h-3z" fill="#fff"/></svg>
</div>
</body>
</html>
```